Brimlow OrthoLink IT Inc. new website

i need a website for my company which is dedicated to installation and service of computer systems in Dental Offices. I would like for it to encompass a technology feel and professional look. The company deals with all aspects of technology like, Audio Visual, computer systems and networks, Cloud services like data backup, data center. We provide manage services, support and services to Dental Professionals.
Updates

Looking for a Technology font but professional look Added Wednesday, April 20, 2016

Target Market(s)

Dental, Dentist

Industry/Entity Type

Dental

Number of Pages Required

5+ page

Font styles to use
Other font styles liked:
• Futuristic or Techy

Colors
0255a3
ec1f27

Requirements
Must have
• Tabs
Nice to have
• Have no idea maybe some suggestion on your part may help
Should not have
• A professional feel but have a techy look

```html
<!DOCTYPE html>
<html lang="en">
<head>
<meta charset="utf-8">
<title>Brimlow OrthoLink IT Inc.</title>
<link href="https://fonts.googleapis.com/css2?family=Montserrat:wght@400;700&family=Roboto+Slab:wght@300;400;700&display=swap" rel="stylesheet">
<style>
:root{
  --blue:#0255a3;
  --red:#ec1f27;
  --ink:#1c1c1c;
  --muted:#8a8a8a;
  --grey-bg:#f6f6f6;
  --white:#ffffff;
  --partner:#7a7a7a;
}
*{margin:0;padding:0;box-sizing:border-box}
html,body{width:1200px;height:3475px;overflow:hidden;background:var(--white)}
body{font-family:"Roboto Slab",Georgia,serif;color:var(--ink);position:relative}
.head{font-family:"Montserrat",Arial,sans-serif;font-weight:700;text-transform:uppercase}
section,header,footer{position:absolute;left:0;width:1200px}
.center{text-align:center}

/* header */
.site-header{top:0;height:95px;display:flex;align-items:center;justify-content:space-between;padding:0 170px 0 200px}
.brand{font-family:"Montserrat",Arial,sans-serif;font-weight:700;font-size:22px;color:var(--blue);display:flex;align-items:center;gap:10px}
.brand-mark{width:22px;height:22px;background:var(--blue)}
.nav{display:flex;gap:34px;font-family:"Montserrat",Arial,sans-serif;font-size:12px;color:#666;text-transform:uppercase}
.nav .active{color:var(--red)}

/* hero */
.hero{top:95px;height:458px;background:linear-gradient(100deg,#3d77c2,#5a8fcf 45%,#2e68b5);color:var(--white)}
.hero-title{margin-top:92px;font-size:46px;line-height:56px;letter-spacing:-.5px}
.hero-sub{margin-top:22px;font-size:15px;font-weight:300}
.btn{display:inline-block;background:var(--red);color:var(--white);font-family:"Montserrat",Arial,sans-serif;font-weight:700;font-size:12px;text-transform:uppercase;border-radius:26px;padding:17px 42px}
.hero .btn{margin-top:44px}
.dots{position:absolute;bottom:26px;left:0;width:100%;display:flex;justify-content:center;gap:8px}
.dots i{width:8px;height:8px;border-radius:50%;background:rgba(255,255,255,.85)}

/* section titles */
.sec-title{font-size:34px;color:var(--red)}
.sec-sub{margin-top:8px;font-size:16px;color:#555;font-weight:300}

/* services */
.services{top:553px;height:457px;padding-top:75px}
.cols{display:flex;justify-content:center;gap:60px;margin-top:78px}
.col{width:225px;text-align:center}
.col svg{height:50px}
.col h3{font-size:14px;line-height:20px;margin-top:24px;min-height:40px;display:flex;align-items:flex-end;justify-content:center}
.col p{margin-top:28px;font-size:11.5px;line-height:17px;color:var(--muted);font-weight:300}

/* provide */
.provide{top:1010px;height:527px;background:#e6e6e6}
.provide-photo{position:absolute;left:368px;top:0;width:832px;height:527px;background:linear-gradient(110deg,#1f5fb0,#3f7cc8 55%,#6a9bd6)}
.provide-text{position:absolute;left:455px;top:70px;width:560px;color:var(--white)}
.provide-text h2{font-size:32px}
.provide-text h3{font-size:21px;line-height:30px;margin-top:4px}
.provide-text p{margin-top:14px;font-size:12.5px;line-height:19px;font-weight:300;width:390px}
.checks{list-style:none;margin-top:14px}
.checks li{display:flex;align-items:center;gap:14px;font-size:12.5px;font-weight:300;height:37px}
.provide .btn{margin-top:40px;padding:17px 34px}

/* culture */
.culture{top:1537px;height:475px;background:var(--grey-bg);padding-top:70px}
.values{position:relative;margin:60px auto 0;width:900px;height:230px}
.connector{position:absolute;top:45px;height:2px;background:#777}
.value{position:absolute;top:0;width:240px;text-align:center}
.ring{width:84px;height:84px;border-radius:50%;border:2px solid #777;margin:0 auto;display:flex;align-items:center;justify-content:center;background:var(--grey-bg)}
.value h3{font-size:14px;margin-top:26px}
.value p{margin-top:12px;font-size:11.5px;line-height:17px;color:var(--muted);font-weight:300}

/* clients */
.clients{top:2012px;height:693px;padding-top:78px}
.avatar{position:absolute;width:190px;height:190px;border-radius:50%;background:radial-gradient(circle at 50% 40%,#e9c2a8,#b55a4a 70%,#d8d8d8);border:5px solid #eee}
.quote{position:absolute;background:#f2f2f2;padding:28px 30px;text-align:center;font-size:18px;line-height:27px;color:#444;font-weight:300}
.quote cite{display:block;margin-top:8px;font-size:13px;font-style:normal;color:var(--red)}

/* cta */
.cta{top:2705px;height:215px;background:var(--red);color:var(--white);padding-top:72px}
.cta h2{font-size:34px}
.btn-outline{display:inline-block;margin-top:22px;border:2px solid var(--white);color:var(--white);font-family:"Montserrat",Arial,sans-serif;font-weight:700;font-size:13px;text-transform:uppercase;padding:12px 26px;border-radius:4px}

/* partners */
.partners{top:2920px;height:130px;display:flex;align-items:center;justify-content:center;gap:80px;font-family:"Montserrat",Arial,sans-serif;font-weight:700;font-size:22px;color:var(--partner)}

/* footer */
.site-footer{top:3050px;height:320px;background:var(--blue);border-top:10px solid var(--red);color:var(--white);display:flex;padding:58px 0 0 197px}
.fcol h4{font-family:"Montserrat",Arial,sans-serif;font-weight:700;font-size:14px;text-transform:uppercase;margin-bottom:20px}
.fcol{font-size:12px;line-height:18px;font-weight:300}
.fcol.contact{width:269px}
.fcol.posts{width:287px}
.row{display:flex;gap:16px;margin-bottom:18px;align-items:flex-start}
.posts .row{margin-bottom:16px}
.tweet{display:flex;gap:12px;margin-bottom:16px;width:230px}
.tweet b{font-weight:700;display:block}
.tweet small{font-size:9px;opacity:.8}

.bottom{top:3370px;height:105px;text-align:center;padding-top:38px}
.socials{display:flex;justify-content:center;gap:10px}
.socials i{width:30px;height:30px;border-radius:50%;display:block}
.copyright{margin-top:12px;font-size:11px;color:#555}
</style>
</head>
<body>

<header class="site-header">
  <div class="brand"><span class="brand-mark"></span>Brimlow OrthoLink IT</div>
  <nav class="nav"><span class="active">Home</span><span>About</span><span>Blog</span><span>Portfolio</span><span>Contact</span></nav>
</header>

<section class="hero center" role="img" aria-label="Blue-tinted photo of a dental professional in an office">
  <h1 class="head hero-title">Our company is<br>dedicated to installation</h1>
  <p class="hero-sub">service of computer systema in Dental Offices.</p>
  <span class="btn">Learn more</span>
  <div class="dots"><i></i><i></i><i></i></div>
</section>

<section class="services center">
  <h2 class="head sec-title">Our services</h2>
  <p class="sec-sub">Proin iaculis purus consequat sem cure</p>
  <div class="cols">
    <div class="col">
      <svg viewBox="0 0 40 50" width="40" fill="none" stroke="#8a8a8a" stroke-width="2"><rect x="13" y="4" width="14" height="26" rx="7"/><path d="M7 24a13 13 0 0 0 26 0M20 37v9"/></svg>
      <h3 class="head">Audio visual</h3>
      <p>Proin iaculis purus consequat sem cure digni ssim. Donec porttitora entum suscipit aenean rhoncus posuere odio in tincidunt.</p>
    </div>
    <div class="col">
      <svg viewBox="0 0 60 50" width="60" fill="none" stroke="#8a8a8a" stroke-width="2"><rect x="22" y="3" width="16" height="11"/><rect x="4" y="32" width="16" height="11"/><rect x="22" y="32" width="16" height="11"/><rect x="40" y="32" width="16" height="11"/><path d="M30 14v9M12 32v-9h36v9M30 23v9"/></svg>
      <h3 class="head">Computer systems<br>and networks</h3>
      <p>Proin iaculis purus consequat sem cure digni ssim. Donec porttitora entum suscipit aenean rhoncus posuere odio in tincidunt.</p>
    </div>
    <div class="col">
      <svg viewBox="0 0 56 50" width="56" fill="none" stroke="#8a8a8a" stroke-width="2"><path d="M14 26a9 9 0 0 1 2-18 12 12 0 0 1 22 2 8 8 0 0 1 4 16"/><ellipse cx="28" cy="26" rx="12" ry="4"/><path d="M16 26v16c0 2 5 4 12 4s12-2 12-4V26M16 34c0 2 5 4 12 4s12-2 12-4"/></svg>
      <h3 class="head">Cloud services of<br>data backup</h3>
      <p>Proin iaculis purus consequat sem cure digni ssim. Donec porttitora entum suscipit aenean rhoncus posuere odio in tincidunt.</p>
    </div>
  </div>
</section>

<section class="provide">
  <div class="provide-photo" role="img" aria-label="Blue-tinted photo of dentists treating a patient"></div>
  <div class="provide-text">
    <h2 class="head">We provide</h2>
    <h3 class="head">Manage services, support and service to<br>dental professionals.</h3>
    <p>Proin iaculis purus consequat sem cure digni ssim. Donec porttitora entum suscipit aenean rhoncus posuere odio in tincidunt.</p>
    <ul class="checks">
      <li><svg width="24" height="24" viewBox="0 0 24 24" fill="none" stroke="#fff" stroke-width="1.5"><circle cx="12" cy="12" r="10.5"/><path d="M7 12l3.5 3.5L17 9"/></svg>Initial Setup &amp; Customizations</li>
      <li><svg width="24" height="24" viewBox="0 0 24 24" fill="none" stroke="#fff" stroke-width="1.5"><circle cx="12" cy="12" r="10.5"/><path d="M7 12l3.5 3.5L17 9"/></svg>Regular Updates</li>
      <li><svg width="24" height="24" viewBox="0 0 24 24" fill="none" stroke="#fff" stroke-width="1.5"><circle cx="12" cy="12" r="10.5"/><path d="M7 12l3.5 3.5L17 9"/></svg>Round The Clock Support</li>
    </ul>
    <span class="btn">Learn more</span>
  </div>
</section>

<section class="culture center">
  <h2 class="head sec-title">Culture &amp; values</h2>
  <p class="sec-sub">Proin iaculis purus consequat cure.</p>
  <div class="values">
    <div class="connector" style="left:148px;width:170px"></div>
    <div class="connector" style="left:430px;width:190px"></div>
    <div class="value" style="left:-30px">
      <div class="ring"><svg width="32" height="32" viewBox="0 0 32 32" fill="#777"><path d="M14 2h4l1 4 3 1.3 3.5-2.2 2.8 2.8-2.2 3.5L27 14l4 1v2l-4 1-1.3 3 2.2 3.5-2.8 2.8-3.5-2.2L18 26.4 17 31h-2l-1-4.6-3-1.3-3.5 2.2-2.8-2.8 2.2-3.5L6 18l-4-1v-2l4-1 1.3-3-2.2-3.5 2.8-2.8L11 6.6 14 5.3z"/><circle cx="16" cy="16" r="5" fill="#f6f6f6"/></svg></div>
      <h3 class="head">Manage services</h3>
      <p>Proin iaculis purus consequat sem cure digni ssim. Donec porttitora entum suscipit aenean rhoncus posuere odio in tincidunt.</p>
    </div>
    <div class="value" style="left:255px">
      <div class="ring"><svg width="34" height="34" viewBox="0 0 34 34" fill="none" stroke="#777" stroke-width="3"><circle cx="17" cy="17" r="14"/><circle cx="17" cy="17" r="6"/><path d="M7 7l6 6M27 7l-6 6M7 27l6-6M27 27l-6-6"/></svg></div>
      <h3 class="head">Support</h3>
      <p>Proin iaculis purus consequat sem cure digni ssim. Donec porttitora entum suscipit aenean rhoncus posuere odio in tincidunt.</p>
    </div>
    <div class="value" style="left:540px">
      <div class="ring"><svg width="34" height="34" viewBox="0 0 34 34" fill="#777"><circle cx="17" cy="11" r="7"/><path d="M4 32c0-8 6-12 13-12s13 4 13 12z"/></svg></div>
      <h3 class="head">Dental professionals</h3>
      <p>Proin iaculis purus consequat sem cure digni ssim. Donec porttitora entum suscipit aenean rhoncus posuere odio in tincidunt.</p>
    </div>
  </div>
</section>

<section class="clients center">
  <h2 class="head sec-title">Our awesome clients</h2>
  <p class="sec-sub">Proin iaculis purus consequat sem cure.</p>
  <div class="avatar" role="img" aria-label="Portrait photo of client Dana Whitfield" style="left:195px;top:218px"></div>
  <blockquote class="quote" style="left:422px;top:245px;width:553px">“ Proin iaculis purus consequat sem cure &nbsp;digni ssim donec porttitora entum suscipit aenean rhoncus. ”<cite>- Dana Whitfield, Founder of Larkspur Media</cite></blockquote>
  <blockquote class="quote" style="left:228px;top:455px;width:552px">“ Proin iaculis purus consequat sem cure &nbsp;digni ssim donec porttitora entum suscipit aenean rhoncus. ”<cite>- Nora Ellery, Founder of Quillmont</cite></blockquote>
  <div class="avatar" role="img" aria-label="Portrait photo of client Nora Ellery" style="left:810px;top:445px"></div>
</section>

<section class="cta center">
  <h2 class="head">Ready to talk about your next project?</h2>
  <span class="btn-outline">Contact us</span>
</section>

<section class="partners">
  <span class="partner-name">Northvane</span>
  <span class="partner-name">Calder Group</span>
  <span class="partner-name">Meridex</span>
  <span class="partner-name">Holloway</span>
</section>

<footer class="site-footer">
  <div class="fcol contact">
    <h4>Contact us</h4>
    <div class="row"><svg width="18" height="24" viewBox="0 0 18 24" fill="#fff"><path d="M9 0a9 9 0 0 0-9 9c0 7 9 15 9 15s9-8 9-15a9 9 0 0 0-9-9zm0 12a3 3 0 1 1 0-6 3 3 0 0 1 0 6z"/></svg><span>18 Harbour Rd.<br>Kelso, ON<br>K2P 4B7</span></div>
    <div class="row"><svg width="18" height="24" viewBox="0 0 18 24" fill="none" stroke="#fff" stroke-width="2"><rect x="3" y="1" width="12" height="22" rx="2"/><path d="M8 19h2"/></svg><span>(613) 555-0148</span></div>
    <div class="row"><svg width="18" height="14" viewBox="0 0 18 14" fill="#fff"><path d="M0 0h18v14H0z"/><path d="M1 1l8 6 8-6" stroke="#0255a3" fill="none" stroke-width="1.5"/></svg><span>hello@brimlowortholink.com</span></div>
  </div>
  <div class="fcol posts">
    <h4>Latest posts</h4>
    <div class="row"><svg width="18" height="14" viewBox="0 0 18 14" fill="none" stroke="#fff" stroke-width="2"><rect x="1" y="1" width="16" height="12"/><path d="M4 5h4M4 9h10"/></svg>Made With Love In Kelso</div>
    <div class="row"><svg width="18" height="14" viewBox="0 0 18 14" fill="none" stroke="#fff" stroke-width="2"><rect x="1" y="1" width="16" height="12"/><path d="M4 5h4M4 9h10"/></svg>Startup News &amp; Emerging Tech</div>
    <div class="row"><svg width="18" height="14" viewBox="0 0 18 14" fill="none" stroke="#fff" stroke-width="2"><rect x="1" y="1" width="16" height="12"/><path d="M4 5h4M4 9h10"/></svg>Bitcoin Will Soon Rule The World</div>
    <div class="row"><svg width="18" height="14" viewBox="0 0 18 14" fill="none" stroke="#fff" stroke-width="2"><rect x="1" y="1" width="16" height="12"/><path d="M4 5h4M4 9h10"/></svg>Wearable Technology On The Rise</div>
    <div class="row"><svg width="18" height="14" viewBox="0 0 18 14" fill="#fff"><path d="M3 0l13 7-13 7z"/></svg>Learn Web Design In 30 Days!</div>
  </div>
  <div class="fcol">
    <h4>Latest tweets</h4>
    <div class="tweet"><svg width="16" height="14" viewBox="0 0 16 14" fill="#fff"><path d="M0 2l6 5-2 5 12-5V0z"/></svg><div>Old proverb: Life is really simple, but we insist on making it complicated.<b>#loriumipsum</b><small>8 mins ago</small></div></div>
    <div class="tweet"><svg width="16" height="14" viewBox="0 0 16 14" fill="#fff"><path d="M0 2l6 5-2 5 12-5V0z"/></svg><div>Grab the Free lorium ipsum dolor amit deo. seu dfokal<b>#loriumipsum</b><small>2 days ago</small></div></div>
  </div>
</footer>

<section class="bottom">
  <div class="socials">
    <i style="background:#1fa8e0"></i><i style="background:#3a5ba0"></i><i style="background:#cb2027"></i><i style="background:#dc4a38"></i>
  </div>
  <p class="copyright">© Copyright 2016. www.brimlowortholink.com</p>
</section>

</body>
</html>
```